Larkfield Ridge Management

I need a professional website. My current website is larkfieldridgemanagement.com and I hate it. It was created with some AI tool very quickly because I needed a site up and running with no advanced notice. I’m open to all designs .. I trust you, the professionals will deliver the results I’m anxiously awaiting! :)

```html
<!DOCTYPE html>
<html lang="en">
<head>
<meta charset="utf-8">
<title>Larkfield Ridge Management</title>
<link rel="stylesheet" href="https://fonts.googleapis.com/css2?family=Montserrat:wght@600;700&family=Lato:wght@400;700&display=swap">
<style>
:root{
  --navy:#243a68;
  --navy-deep:#1d2f56;
  --red:#d1232a;
  --ink:#2b2b2b;
  --muted:#444;
  --line:#e3e3e3;
  --white:#fff;
}
*{margin:0;padding:0;box-sizing:border-box}
html,body{width:1200px;height:3486px;overflow:hidden}
body{position:relative;font-family:'Lato',sans-serif;color:var(--ink);background:var(--white)}
.abs{position:absolute}
h1,h2,h3{font-family:'Montserrat',sans-serif;font-weight:700}
.btn{position:absolute;display:flex;align-items:center;justify-content:center;font-family:'Lato',sans-serif;font-size:17px;color:var(--white);background:var(--red)}
.rule{position:absolute;height:3px;background:var(--red)}
.center{left:0;width:1200px;text-align:center}

/* hero */
.hero-bg{left:0;top:0;width:1200px;height:685px;background:linear-gradient(180deg,#6b80b8 0%,#8a7f9a 18%,#5b5f6e 40%,#3c4450 58%,#3d5a2a 76%,#2f4a1f 100%)}
.header{left:0;top:41px;width:1200px;height:85px;background:var(--white);box-shadow:0 1px 3px rgba(0,0,0,.12)}
.brand-tab{left:112px;top:11px;width:122px;height:140px;background:var(--white);border-radius:0 0 61px 61px;display:flex;flex-direction:column;align-items:center;justify-content:center;gap:8px}
.brand-tab .sq{width:14px;height:14px;background:var(--red)}
.brand-tab span{font-family:'Montserrat',sans-serif;font-weight:700;font-size:14px;line-height:1.2;color:var(--navy);text-align:center}
.nav a{position:absolute;top:74px;font-size:15px;color:#333;text-decoration:none}
.hero-panel{left:234px;top:234px;width:756px;height:298px;background:rgba(40,48,70,.55)}
.hero-title{top:232px;font-size:54px;line-height:64px;color:var(--white)}
.hero-text{top:374px;font-size:17px;line-height:26px;color:var(--white)}

/* about */
.about-photo{left:111px;top:781px;width:446px;height:393px;background:linear-gradient(135deg,#cfc6b8 0%,#b9ad9b 45%,#8d8070 100%);box-shadow:0 2px 6px rgba(0,0,0,.25)}
.about-bar{left:89px;top:806px;width:22px;height:347px;background:var(--red)}
.about-title{left:639px;top:766px;font-size:40px;line-height:51px;color:var(--navy)}
.about-copy{left:643px;width:445px;font-size:15px;line-height:25.7px;color:var(--muted);text-align:justify}

/* services */
.band{left:0;width:1200px;background:linear-gradient(180deg,rgba(36,58,104,.96),rgba(30,49,90,.94)),linear-gradient(90deg,#3b4d74,#2a3b61)}
.card{position:absolute;top:1557px;width:231px;height:310px;background:var(--white)}
.card .ph{position:absolute;left:6px;top:6px;width:219px;height:247px}
.card h3{position:absolute;left:0;top:268px;width:100%;text-align:center;font-family:'Lato',sans-serif;font-weight:700;font-size:18px;color:#111}

/* proposal */
.map{left:111px;top:2218px;width:446px;height:276px;background:linear-gradient(135deg,#a8d8ea,#bfe3ee 50%,#e8ece6);box-shadow:0 1px 4px rgba(0,0,0,.2)}
.info{font-size:15px;color:#333;display:flex;align-items:center;gap:10px}
.form{left:644px;top:2218px;width:446px;height:353px;background:var(--white);box-shadow:0 0 6px rgba(0,0,0,.14)}
.field{position:absolute;left:674px;width:387px;height:47px;border:1px solid #e6e6e6;box-shadow:0 1px 4px rgba(0,0,0,.08);display:flex;align-items:center;gap:10px;padding-left:22px;font-size:15px;color:#666}
.submit{left:680px;top:2500px;width:137px;height:46px;background:#444;font-weight:700;font-size:18px}

/* footer */
.footer h3{font-size:18px;font-weight:600;color:var(--navy)}
.links li{position:absolute;left:371px;list-style:none;font-size:14.5px;color:#333}
.links li::before{content:"";position:absolute;left:-19px;top:6px;width:7px;height:7px;border-radius:50%;background:var(--red)}
.fcontact{position:absolute;left:818px;font-size:15px;color:#333;display:flex;align-items:center;gap:8px}
.ico{width:18px;height:18px;flex:none}
.copy{left:0;top:3439px;width:1200px;height:47px;background:var(--red);color:var(--white);font-size:15px;display:flex;align-items:center;justify-content:center}
</style>
</head>
<body>

<!-- Hero -->
<div class="abs hero-bg" role="img" aria-label="Modern apartment complex at dusk with lit windows and a green lawn"></div>
<div class="abs header"></div>
<div class="abs brand-tab"><div class="sq"></div><span>Larkfield Ridge<br>Management</span></div>
<nav class="nav">
  <a style="left:720px">Home</a>
  <a style="left:791px">Services</a>
  <a style="left:877px">About</a>
</nav>
<div class="btn" style="left:963px;top:58px;width:126px;height:46px">Contact Us</div>
<div class="abs hero-panel"></div>
<h1 class="abs center hero-title">A true partner<br>not just a vendor</h1>
<p class="abs center hero-text">Protect your investment with dependable property management services tailored for property<br>owners throughout Cleveland and Akron. From tenant relations to maintenance coordination,<br>we help maximize value while minimizing stress.</p>
<div class="btn" style="left:538px;top:471px;width:126px;height:46px">Contact Us</div>

<!-- About -->
<section class="about">
  <div class="abs about-bar"></div>
  <div class="abs about-photo" role="img" aria-label="Warm-toned bathroom vanity with a round mirror and dark faucet"></div>
  <h2 class="abs about-title">About Our Property<br>Management Solutions</h2>
  <div class="rule" style="left:643px;top:885px;width:188px"></div>
  <p class="abs about-copy" style="top:913px">Our organization delivers comprehensive property management solutions that optimize asset performance and tenant satisfaction. By integrating advanced analytics with proven operational frameworks, our specialists ensure each property achieves sustained value appreciation.</p>
  <p class="abs about-copy" style="top:1052px">Drawing on decades of collective expertise, the team facilitates regulatory compliance, cost efficiency, and proactive maintenance. This disciplined approach enables owners to preserve capital, enhance occupancy rates, and demonstrate long-term resilience across diverse market conditions.</p>
</section>

<!-- Services -->
<section class="abs band" style="top:1262px;height:692px"></section>
<h2 class="abs center" style="top:1336px;font-size:41px;color:#fff">Strategic Property Management Solutions</h2>
<div class="rule" style="left:505px;top:1402px;width:189px"></div>
<p class="abs center" style="top:1425px;color:#fff;font-size:15.5px;line-height:25.7px">Our analysis demonstrates that effective property oversight originates from meticulous operational planning, transparent<br>communication channels, and data-driven performance metrics across every asset class. By integrating advanced technology with<br>industry expertise, our team implements proactive maintenance schedules that preserve asset value and facilitate sustainable,<br>long-term returns for stakeholders.</p>
<div class="card" style="left:111px"><div class="ph" role="img" aria-label="Hands arranging material samples on a wooden table" style="background:linear-gradient(135deg,#d9c6ad,#a98d6f)"></div><h3>Basic Service</h3></div>
<div class="card" style="left:360px"><div class="ph" role="img" aria-label="Table lamp beside an open book on a dark shelf" style="background:linear-gradient(180deg,#d8c3aa 0%,#c8ae90 72%,#2a2520 74%)"></div><h3>Intermediate Service</h3></div>
<div class="card" style="left:607px"><div class="ph" role="img" aria-label="Desk with a calla lily vase and a small lamp" style="background:linear-gradient(135deg,#b49c82,#e4d8c8 60%,#cbbba6)"></div><h3>Advanced Service</h3></div>
<div class="card" style="left:856px"><div class="ph" role="img" aria-label="High-rise residential tower at sunset" style="background:linear-gradient(180deg,#5c79b0,#c98a6c 55%,#2b3a2a)"></div><h3>Advanced+ Service</h3></div>

<!-- Proposal -->
<h2 class="abs center" style="top:2051px;font-size:41px;color:var(--navy)">Request a Tailored Proposal</h2>
<div class="rule" style="left:505px;top:2120px;width:189px"></div>
<p class="abs center" style="top:2149px;font-size:15px;color:#333">Submit the form to initiate a consultative assessment and explore solutions aligned with your objectives.</p>
<div class="abs map" role="img" aria-label="Map showing office locations in Cleveland and Akron, Ohio"></div>
<div class="abs info" style="left:111px;top:2513px">
  <svg class="ico" viewBox="0 0 20 20"><circle cx="10" cy="10" r="10" fill="#d1232a"/><path d="M7 5.5l2 2-1 1.3a6 6 0 0 0 3.2 3.2l1.3-1 2 2-1.2 1.5c-3.5 0-7.5-4-7.5-7.5z" fill="#fff"/></svg>+1 555 014 2290</div>
<div class="abs info" style="left:308px;top:2513px">
  <svg class="ico" viewBox="0 0 20 20"><circle cx="10" cy="10" r="10" fill="#d1232a"/><path d="M10 4a4 4 0 0 1 4 4c0 3-4 7-4 7s-4-4-4-7a4 4 0 0 1 4-4z" fill="#fff"/><circle cx="10" cy="8" r="1.5" fill="#d1232a"/></svg>Larkfield Ridge Management LLC</div>
<div class="abs info" style="left:111px;top:2552px">
  <svg class="ico" viewBox="0 0 20 20"><circle cx="10" cy="10" r="10" fill="#d1232a"/><rect x="5" y="6.5" width="10" height="7" fill="#fff"/><path d="M5 6.5l5 4 5-4" stroke="#d1232a" fill="none"/></svg>info@larkfieldridgemanagement.com</div>
<div class="abs form"></div>
<div class="field" style="top:2242px"><svg class="ico" viewBox="0 0 20 20"><circle cx="10" cy="6" r="4" fill="#777"/><path d="M2 19c0-5 4-7 8-7s8 2 8 7z" fill="#777"/></svg>Name</div>
<div class="field" style="top:2307px"><svg class="ico" viewBox="0 0 20 20"><rect x="1" y="4" width="18" height="12" fill="#777"/><path d="M1 4l9 7 9-7" stroke="#fff" fill="none"/></svg>Email</div>
<div class="field" style="top:2370px"><svg class="ico" viewBox="0 0 20 20"><rect x="2" y="3" width="16" height="14" fill="none" stroke="#777" stroke-width="2"/><path d="M5 8h10M5 12h7" stroke="#777" stroke-width="2"/></svg>Message</div>
<div class="field" style="top:2434px"><svg class="ico" viewBox="0 0 20 20"><path d="M4 2l4 4-2 2.5a11 11 0 0 0 5.5 5.5L14 12l4 4-2.5 2.5C8.5 18.5 1.5 11.5 1.5 4.5z" fill="#777"/></svg>Phone Number</div>
<div class="btn submit">Submit</div>

<!-- CTA -->
<section class="abs band" style="top:2676px;height:425px"></section>
<h2 class="abs center" style="top:2746px;font-size:41px;color:#fff">Protect Your Investment with Confidence</h2>
<div class="rule" style="left:505px;top:2813px;width:189px"></div>
<p class="abs center" style="top:2846px;color:#fff;font-size:15.5px;line-height:26px">Whether you own a single rental property or a growing real estate portfolio, Larkfield Ridge Management LLC is committed to<br>delivering reliable, proactive management that preserves value, enhances tenant satisfaction, and simplifies property ownership.</p>
<p class="abs center" style="top:2917px;color:#fff;font-size:15.5px">Let us handle the day-to-day operations while you enjoy the benefits of stress-free property ownership.</p>
<div class="btn" style="left:337px;top:2970px;width:246px;height:45px">Request a Tailored Proposal</div>
<div class="btn" style="left:605px;top:2970px;width:254px;height:45px;background:transparent;border:2px solid #fff">Schedule a Free Consultation</div>

<!-- Footer -->
<footer class="footer">
  <div class="abs" style="left:111px;top:3225px;width:150px;display:flex;align-items:center;gap:8px">
    <div style="width:14px;height:14px;background:var(--red);flex:none"></div>
    <span style="font-family:'Montserrat',sans-serif;font-weight:700;font-size:17px;line-height:1.2;color:var(--navy)">Larkfield Ridge<br>Management</span>
  </div>
  <h3 class="abs" style="left:348px;top:3191px">Quick Links</h3>
  <ul class="links">
    <li style="top:3228px">Home</li>
    <li style="top:3262px">About Us</li>
    <li style="top:3297px">Services</li>
    <li style="top:3330px">Contact Us</li>
    <li style="top:3365px">Request a Proposal</li>
  </ul>
  <h3 class="abs" style="left:536px;top:3192px">Newsletter</h3>
  <p class="abs" style="left:539px;top:3228px;width:210px;font-size:14.5px;line-height:22px;color:#333">Subscribe to our latest newsletter to get news about special discounts.</p>
  <div class="abs" style="left:540px;top:3310px;width:220px;height:42px;background:var(--navy);color:#fff;font-size:15px;padding:12px 0 0 24px">Email</div>
  <div class="btn" style="left:540px;top:3361px;width:118px;height:42px;font-weight:700;font-size:17px">Subscribe</div>
  <h3 class="abs" style="left:813px;top:3191px">Contact Us</h3>
  <div class="fcontact" style="top:3228px"><svg class="ico" viewBox="0 0 20 20"><circle cx="10" cy="10" r="10" fill="#d1232a"/><path d="M10 4a4 4 0 0 1 4 4c0 3-4 7-4 7s-4-4-4-7a4 4 0 0 1 4-4z" fill="#fff"/></svg>Larkfield Ridge Management LLC</div>
  <div class="fcontact" style="top:3268px"><svg class="ico" viewBox="0 0 20 20"><circle cx="10" cy="10" r="10" fill="#d1232a"/><rect x="5" y="6.5" width="10" height="7" fill="#fff"/></svg>info@larkfieldridgemanagement.com</div>
  <div class="fcontact" style="top:3313px"><svg class="ico" viewBox="0 0 20 20"><circle cx="10" cy="10" r="10" fill="#d1232a"/><path d="M7 5.5l2 2-1 1.3a6 6 0 0 0 3.2 3.2l1.3-1 2 2-1.2 1.5c-3.5 0-7.5-4-7.5-7.5z" fill="#fff"/></svg>+1 555 014 2290</div>
  <div class="fcontact" style="top:3358px"><svg class="ico" viewBox="0 0 20 20"><circle cx="10" cy="10" r="10" fill="#d1232a"/><path d="M10 5v5l3 2" stroke="#fff" stroke-width="2" fill="none"/></svg>9–17 Opening hours</div>
  <div class="abs copy">© 2026 Larkfield Ridge Management LLC. All Rights Reserved.</div>
</footer>

</body>
</html>
```